Copperleaf Balustrade Website Redesign

I want a fresh new design for my website. Original website
www.copperleafbalustrade-example.com. Will need to add additional photos for winning designer. Please use the basic layout for new design. Looking to get a more modern, functional site to attract new customer and ne bale to highlight past projects. Need it to be easy to navigate and get in touch with me for inquiries.

Target Market(s)

Builders and home owners in WA state

Industry/Entity Type

Building, Construction, Deck building

Coding

Coded - Design and coding required

Number of Pages Required

5+ page

Font styles to use
Sans Serif

Colors
0054AA
0677BA
7BADD7
CADEEF
E8F1F8
0094D4
00A9DD
6FCCEA
C7EBF8
E9F6FB
00AB8E
00BBA5
67D7C9
C6EFE9
E9F9F6
59FF00
82FF00
B8FF75
E3FFCB
F4FFEA

Requirements
Must have
• Will need to add more photos of completed projects
Nice to have
• Fresh take on old website, something modern
Should not have
• Nothing comes to mind

```html
<!DOCTYPE html>
<html lang="en">
<head>
<meta charset="utf-8">
<title>Copperleaf Balustrade</title>
<link href="https://fonts.googleapis.com/css2?family=Roboto:wght@400;500;700;900&display=swap" rel="stylesheet">
<style>
:root{
  --blue:#0b3fa6;
  --blue-deep:#062f86;
  --blue-bright:#0677ba;
  --ink:#1b1b1b;
  --text:#555b66;
  --pale:#e8f1f8;
  --footer:#0d0d0f;
  --white:#ffffff;
}
*{margin:0;padding:0;box-sizing:border-box}
html,body{width:1200px;height:4942px;overflow:hidden}
body{position:relative;font-family:'Roboto',sans-serif;color:var(--ink);background:var(--white)}
.abs{position:absolute}
.photo{position:absolute;overflow:hidden}
h2.section-title{position:absolute;left:0;width:1200px;text-align:center;font-size:37px;font-weight:700;letter-spacing:.3px;color:var(--ink)}
.btn{position:absolute;display:flex;align-items:center;justify-content:center;color:#fff;font-size:14px;font-weight:700;background:var(--blue);clip-path:polygon(8% 0,100% 0,92% 100%,0 100%)}

/* top bar & nav */
.topbar{left:0;top:0;width:1200px;height:60px;background:var(--blue);color:#fff;font-size:14px}
.topbar .license{left:112px;top:22px}
.topbar .contact{top:20px;display:flex;align-items:center;gap:10px}
.nav{left:0;top:60px;width:1200px;height:73px;background:#fff;box-shadow:0 2px 6px rgba(0,0,0,.08);z-index:3}
.nav ul{position:absolute;top:28px;display:flex;list-style:none;font-size:14px;font-weight:500;color:#222}
.nav li{padding:0 20px;border-left:1px solid #333;line-height:14px}
.nav li:first-child{border-left:none;padding-left:0}
.nav li.active{color:var(--blue)}
.logo-plate{left:508px;top:0;width:184px;height:205px;background:#fff;clip-path:polygon(0 0,100% 0,100% 84%,50% 100%,0 84%);z-index:4;box-shadow:0 4px 10px rgba(0,0,0,.2);display:flex;flex-direction:column;align-items:center;justify-content:center;gap:10px}
.logo-plate span{font-size:21px;font-weight:700;color:var(--blue-deep);text-align:center;line-height:1.1}
.logo-plate i{display:block;width:44px;height:44px;background:var(--blue-deep)}

/* hero */
.hero{left:0;top:133px;width:1200px;height:600px;background:linear-gradient(160deg,#3a4048 0%,#23272d 45%,#121417 100%)}
.hero-text{left:0;top:300px;width:1200px;text-align:center;color:#fff;z-index:2}
.hero-text .kicker{font-size:28px;font-weight:700;letter-spacing:.5px}
.hero-text h1{font-size:52px;font-weight:700;line-height:60px;margin-top:14px;letter-spacing:.5px}

/* about */
.about-text{left:693px;top:875px;width:400px}
.about-text h2{font-size:37px;font-weight:700}
.about-text p{margin-top:22px;font-size:14px;line-height:31px;color:var(--text)}

/* products */
.subtitle{position:absolute;left:0;width:1200px;text-align:center;font-size:17px;color:var(--text)}
.card{position:absolute;top:1473px;width:314px;height:402px;background:#fff;border-radius:12px;box-shadow:0 4px 18px rgba(0,0,0,.09)}
.card.featured{border:2px solid var(--blue-bright)}
.card .photo{left:9px;top:9px;width:296px;height:205px;border-radius:6px}
.card .tag{position:absolute;left:50%;top:196px;transform:translateX(-50%);width:198px;height:40px;background:#fff;border-radius:6px;box-shadow:0 2px 8px rgba(0,0,0,.12);display:flex;align-items:center;justify-content:center;font-size:14px;font-weight:500;color:var(--blue)}
.card.featured .tag{background:var(--blue);color:#fff}
.card p{position:absolute;left:30px;right:30px;top:256px;text-align:center;font-size:13px;line-height:24px;color:var(--text)}
.dot-btn{position:absolute;top:1916px;width:40px;height:40px;border-radius:50%;background:#cfe0f4;color:var(--blue);display:flex;align-items:center;justify-content:center;font-size:15px;font-weight:700}

/* cta */
.cta-text{left:0;top:2090px;width:1200px;text-align:center;color:#fff}
.cta-text h2{font-size:37px;font-weight:700;letter-spacing:.3px}
.cta-text p{width:760px;margin:22px auto 0;font-size:16px;line-height:33px}

/* why choose */
.why h2{position:absolute;left:112px;top:2505px;font-size:37px;font-weight:700}
.feature{position:absolute;left:112px;width:460px}
.feature .icon{position:absolute;left:0;top:4px;width:76px;height:76px}
.feature h3{position:absolute;left:104px;top:0;font-size:16px;font-weight:700;color:var(--blue)}
.feature p{position:absolute;left:104px;top:28px;width:360px;font-size:13px;line-height:26px;color:var(--text)}

/* projects */
.project-label{position:absolute;left:36px;bottom:46px;color:#fff;font-size:20px;font-weight:700;letter-spacing:.3px}
.project-go{position:absolute;right:36px;bottom:36px;width:44px;height:44px;border-radius:50%;background:var(--blue-bright);display:flex;align-items:center;justify-content:center}

/* serving */
.serving p{position:absolute;left:170px;top:3902px;width:860px;text-align:center;font-size:17px;line-height:33px;color:var(--text)}

/* footer */
.footer{left:0;top:4535px;width:1200px;height:407px;background:var(--footer);color:#fff}
.footer .brand{position:absolute;left:112px;top:70px;width:150px;text-align:center;font-size:28px;font-weight:400;line-height:1.2}
.footer .brand i{display:block;width:60px;height:60px;margin:16px auto;border:3px solid #fff}
.footer h4{position:absolute;top:82px;font-size:23px;font-weight:700;letter-spacing:.3px}
.footer ul{position:absolute;top:128px;list-style:none;font-size:14px}
.footer li{height:34px;display:flex;align-items:flex-start;gap:14px}
.footer li b{font-weight:400;color:#fff;font-size:13px}
.footer .rule{position:absolute;left:112px;top:286px;width:976px;height:1px;background:#2a2a2e}
.footer .copy{position:absolute;left:112px;top:300px;font-size:13px}
.socials{position:absolute;top:292px;left:915px;display:flex;gap:14px}
.socials span{width:34px;height:34px;border-radius:50%;background:var(--blue)}
.socials span.on{background:#fff}
</style>
</head>
<body>

<!-- top bar -->
<div class="abs topbar">
  <div class="abs license">WA GC LICENSE # <b>COPPELB417KQ</b></div>
  <div class="abs contact" style="left:738px">
    <svg width="14" height="14" viewBox="0 0 24 24"><path fill="#fff" d="M6.6 10.8a15 15 0 006.6 6.6l2.2-2.2a1 1 0 011-.25 11.4 11.4 0 003.6.6 1 1 0 011 1V20a1 1 0 01-1 1A17 17 0 013 4a1 1 0 011-1h3.5a1 1 0 011 1c0 1.25.2 2.45.6 3.6a1 1 0 01-.25 1z"/></svg>
    (555) 014-2290
  </div>
  <div class="abs contact" style="left:908px">
    <svg width="15" height="12" viewBox="0 0 24 18"><path fill="#fff" d="M2 0h20a2 2 0 012 2v14a2 2 0 01-2 2H2a2 2 0 01-2-2V2a2 2 0 012-2zm0 3v1l10 6 10-6V3L12 9z"/></svg>
    hello@copperleafbalustrade-example.com
  </div>
</div>

<nav class="abs nav">
  <ul style="left:112px">
    <li class="active">HOME</li><li>ABOUT US</li><li>SERVICES</li>
  </ul>
  <ul style="left:740px">
    <li>NEWS</li><li>PRODUCTS</li><li>CONTACT</li>
  </ul>
</nav>

<div class="abs logo-plate">
  <span>COPPERLEAF</span>
  <i></i>
  <span>BALUSTRADE</span>
</div>

<!-- hero -->
<div class="photo hero" role="img" aria-label="Modern house balcony with glass and black metal railing"></div>
<svg class="abs" style="left:0;top:540px;z-index:1" width="1200" height="220" viewBox="0 0 1200 220">
  <polygon points="0,0 600,150 1200,0 1200,220 0,220" fill="#fff"/>
  <polygon points="100,48 600,165 1100,48 1100,56 600,185 100,56" fill="#0b3fa6"/>
  <polygon points="600,125 632,143 632,180 600,198 568,180 568,143" fill="#fff" stroke="#e0e6ef"/>
  <circle cx="600" cy="161" r="12" fill="#0b3fa6"/>
  <path d="M600 154v13M595 162l5 5 5-5" stroke="#fff" stroke-width="2" fill="none"/>
</svg>
<div class="abs hero-text">
  <div class="kicker">COPPERLEAF BALUSTRADE</div>
  <h1>DURABLE, STYLISH, &amp; BUILT FOR<br>THE PACIFIC NORTHWEST</h1>
</div>
<div class="btn" style="left:530px;top:488px;width:142px;height:42px;z-index:2">Get Started</div>

<!-- about -->
<svg class="abs" style="left:0;top:775px" width="420" height="550" viewBox="0 0 420 550">
  <defs><linearGradient id="aboutBlue" x1="0" y1="0" x2="1" y2="1"><stop offset="0" stop-color="#0b4bc0"/><stop offset="1" stop-color="#062f86"/></linearGradient></defs>
  <path d="M130 20 Q165 -10 200 20 L400 230 Q430 270 400 310 L210 515 Q170 555 130 515 L0 380 L0 170 Z" fill="url(#aboutBlue)"/>
</svg>
<div class="photo" role="img" aria-label="Two railing installers on a balcony reviewing a stainless steel railing" style="left:163px;top:845px;width:437px;height:410px;border-radius:26px;background:linear-gradient(135deg,#c9d3dc,#8897a6 55%,#4a5866);box-shadow:0 8px 20px rgba(0,0,0,.18)"></div>
<div class="abs about-text">
  <h2>ABOUT US</h2>
  <p>At Copperleaf Balustrade, we believe that every outdoor space deserves the perfect blend of style, safety, and durability. Serving homeowners, builders, and commercial developers across the Washington State, we specialize in crafting custom railing systems designed to withstand the region's unique climate while enhancing the beauty of your outdoor living spaces.</p>
</div>
<div class="btn" style="left:693px;top:1176px;width:148px;height:42px">Read More</div>

<!-- products -->
<h2 class="section-title" style="top:1358px">OUR PRODUCTS</h2>
<div class="subtitle" style="top:1416px">We offer a wide variety of custom and railing systems designed to meet the needs of every project.</div>

<div class="card" style="left:112px">
  <div class="photo" role="img" aria-label="Balcony with grey aluminum railings against blue sky" style="background:linear-gradient(160deg,#3d7fd6,#9bbbe0 45%,#5a5f66)"></div>
  <div class="tag">Aluminum Railings</div>
  <p>For a sleek, low-maintenance option, our powder-coated aluminum railings provide strength, corrosion resistance, and a modern aesthetic. Available in a range of colors and finishes.</p>
</div>
<div class="card featured" style="left:442px">
  <div class="photo" role="img" aria-label="Bright interior with glass panel railing" style="background:linear-gradient(160deg,#e9edf0,#c8cfc9 50%,#a38a6a)"></div>
  <div class="tag">Glass Railings</div>
  <p>Ideal for breathtaking views and clean lines, our glass railings combine tempered glass with sturdy framing to create an elegant, transparent barrier that maintains the beauty of your surroundings.</p>
</div>
<div class="card" style="left:776px">
  <div class="photo" role="img" aria-label="Staircase with stainless steel cable railing" style="background:linear-gradient(160deg,#f1ece6,#d8cfc4 55%,#b49d86)"></div>
  <div class="tag">Cable Railings</div>
  <p>Our stainless steel cable railing systems offer an unobstructed view, ideal for homes or businesses with scenic landscapes. The minimalist design ensures safety while preserving sightlines.</p>
</div>
<div class="dot-btn" style="left:553px">«</div>
<div class="dot-btn" style="left:606px">»</div>

<!-- cta -->
<svg class="abs" style="left:0;top:1914px" width="1200" height="480" viewBox="0 0 1200 480">
  <defs><linearGradient id="ctaBlue" x1="0" y1="0" x2="1" y2="1"><stop offset="0" stop-color="#0d47b8"/><stop offset="1" stop-color="#062f86"/></linearGradient></defs>
  <polygon points="0,0 600,117 1200,0 1200,361 600,478 0,361" fill="url(#ctaBlue)"/>
</svg>
<div class="abs cta-text">
  <h2>GET IN TOUCH WITH ME FOR INQUIRIES</h2>
  <p>Ready to elevate your space with a custom railing solution that's built to last? Reach out to the Copperleaf Balustrade team for a free consultation. Let us bring your vision to life with craftsmanship, care, and precision.</p>
</div>
<div class="btn" style="left:520px;top:2271px;width:160px;height:42px;background:var(--blue-bright)">Get In Touch</div>

<!-- why choose -->
<section class="why">
  <h2>WHY CHOOSE US?</h2>
  <div class="feature" style="top:2583px">
    <svg class="icon" viewBox="0 0 76 76"><rect x="14" y="14" width="48" height="48" rx="9" transform="rotate(45 38 38)" fill="#0b4bc0"/><circle cx="38" cy="38" r="10" fill="none" stroke="#fff" stroke-width="2"/></svg>
    <h3>Locally Crafted, Regionally Resilient</h3>
    <p>Our railings are designed with the Pacific Northwest's weather in mind—rain, snow, and everything in between.</p>
  </div>
  <div class="feature" style="top:2727px">
    <svg class="icon" viewBox="0 0 76 76"><rect x="14" y="14" width="48" height="48" rx="9" transform="rotate(45 38 38)" fill="#0b4bc0"/><path d="M38 27a8 8 0 015 14v4h-10v-4a8 8 0 015-14z" fill="none" stroke="#fff" stroke-width="2"/></svg>
    <h3>Custom Solutions for Every Need</h3>
    <p>We work closely with you to design and fabricate custom railing systems that perfectly suit your space, style, and functional requirements.</p>
  </div>
  <div class="feature" style="top:2871px">
    <svg class="icon" viewBox="0 0 76 76"><rect x="14" y="14" width="48" height="48" rx="9" transform="rotate(45 38 38)" fill="#0b4bc0"/><path d="M28 38l7 7 13-14" fill="none" stroke="#fff" stroke-width="2.4"/></svg>
    <h3>Expert Installation &amp; Craftsmanship</h3>
    <p>Our skilled craftsmen take pride in delivering exceptional workmanship, while our professional installers</p>
  </div>
  <div class="feature" style="top:3015px">
    <svg class="icon" viewBox="0 0 76 76"><rect x="14" y="14" width="48" height="48" rx="9" transform="rotate(45 38 38)" fill="#0b4bc0"/><circle cx="38" cy="38" r="9" fill="none" stroke="#fff" stroke-width="2"/><circle cx="38" cy="38" r="3" fill="#fff"/></svg>
    <h3>Full-Service Partner</h3>
    <p>From the initial consultation and design process to installation and ongoing maintenance, we are with you every step of the way</p>
  </div>
</section>
<svg class="abs" style="left:860px;top:2640px" width="340" height="580" viewBox="0 0 340 580">
  <defs><linearGradient id="whyBlue" x1="0" y1="0" x2="1" y2="1"><stop offset="0" stop-color="#0d6fd0"/><stop offset="1" stop-color="#062f86"/></linearGradient></defs>
  <path d="M300 0 L340 40 L340 400 L160 560 Q130 590 100 560 L0 460 L0 60 Z" fill="url(#whyBlue)"/>
</svg>
<div class="photo" role="img" aria-label="Dark modern balcony with black-framed glass railing" style="left:623px;top:2503px;width:469px;height:622px;border-radius:28px;background:linear-gradient(170deg,#6b7077,#3a3f45 50%,#1f2226);box-shadow:0 8px 22px rgba(0,0,0,.2)"></div>

<!-- projects -->
<h2 class="section-title" style="top:3248px">OUR PAST PROJECTS</h2>
<div class="photo" role="img" aria-label="Apartment balconies with black metal railings" style="left:-30px;top:3327px;width:243px;height:438px;border-radius:24px;background:linear-gradient(160deg,#c9b89c,#8a7a62 60%,#2f3a2e)"></div>
<div class="photo" role="img" aria-label="Deck with aluminum railing overlooking a valley town" style="left:241px;top:3327px;width:716px;height:438px;border-radius:28px;background:linear-gradient(180deg,#8d98a6 0%,#56624f 45%,#1e2320 80%,#0a0a0a)">
  <div class="project-label">ALUMINUM RAILINGS</div>
  <div class="project-go"><svg width="18" height="18" viewBox="0 0 24 24"><path d="M14 5l7 7-7 7v-4c-6 0-9 2-11 5 1-6 4-10 11-11z" fill="#fff"/></svg></div>
</div>
<div class="photo" role="img" aria-label="Exterior stairs with black metal railing" style="left:985px;top:3327px;width:245px;height:438px;border-radius:24px;background:linear-gradient(160deg,#b9bfc6,#7d8389 55%,#4a4f54)"></div>

<!-- serving -->
<section class="serving">
  <h2 class="section-title" style="top:3833px">SERVING WASHINGTON STATE</h2>
  <p>Copperleaf Balustrade is proud to serve the entire state of Washington. Whether you're upgrading your home's deck or outfitting a commercial space, we understand the importance of creating beautiful, durable railings that stand up to the region's diverse and often challenging weather conditions.</p>
</section>
<svg class="abs" style="left:860px;top:4280px" width="340" height="280" viewBox="0 0 340 280"><ellipse cx="260" cy="260" rx="230" ry="230" fill="#0d0d0f"/></svg>
<div class="abs footer"></div>
<div class="photo" role="img" aria-label="Service area map of the region" style="left:112px;top:4032px;width:976px;height:503px;border-radius:30px;background:linear-gradient(135deg,#e6ecef,#d7e6d9 50%,#dfe7ee);z-index:2"></div>

<!-- footer -->
<footer class="abs footer" style="background:transparent">
  <div class="brand">COPPERLEAF<i></i>BALUSTRADE</div>
  <h4 style="left:400px">QUICK LINKS</h4>
  <ul style="left:400px"><li><b>»</b>Home</li><li><b>»</b>About Us</li><li><b>»</b>Our Products</li><li><b>»</b>Why Choose Us?</li><li><b>»</b>Contact Us</li></ul>
  <h4 style="left:634px">OUR PRODUCTS</h4>
  <ul style="left:634px"><li><b>»</b>Aluminum Railings</li><li><b>»</b>Glass Railings</li><li><b>»</b>Cable Railings</li><li><b>»</b>Custom</li></ul>
  <h4 style="left:886px">CONTACT US</h4>
  <ul style="left:886px">
    <li><svg width="12" height="16" viewBox="0 0 12 16"><path d="M6 0a6 6 0 016 6c0 4.5-6 10-6 10S0 10.5 0 6a6 6 0 016-6zm0 3.5a2.5 2.5 0 100 5 2.5 2.5 0 000-5z" fill="#fff"/></svg>1480 Alder Crest Rd</li>
    <li style="padding-left:26px">Ridgefield, WA 98642</li>
    <li><svg width="13" height="13" viewBox="0 0 24 24"><path fill="#fff" d="M6.6 10.8a15 15 0 006.6 6.6l2.2-2.2a1 1 0 011-.25 11.4 11.4 0 003.6.6 1 1 0 011 1V20a1 1 0 01-1 1A17 17 0 013 4a1 1 0 011-1h3.5a1 1 0 011 1c0 1.25.2 2.45.6 3.6a1 1 0 01-.25 1z"/></svg>(555) 014-2290</li>
    <li><svg width="14" height="11" viewBox="0 0 24 18"><path fill="#fff" d="M2 0h20a2 2 0 012 2v14a2 2 0 01-2 2H2a2 2 0 01-2-2V2a2 2 0 012-2zm0 3v1l10 6 10-6V3L12 9z"/></svg>info@copperleafbalustrade-example.com</li>
  </ul>
  <div class="rule"></div>
  <div class="copy">(C) Copyright 2024 | All Rights Reserved</div>
  <div class="socials"><span></span><span></span><span class="on"></span><span></span></div>
</footer>

</body>
</html>
```